Brivolt Technologies business card design

We need a business card designed with our new logo. it would be great if the card could communicate it is a technology based company.

Target Market(s)

system integrators

Industry/Entity Type

technology, IOT

Contact Information for Business Card

Name, designation, Address, telephone number, email address

Requirements
Must have
• logo and company name
Nice to have
• something to do with technology

```html
<!DOCTYPE html>
<html lang="en">
<head>
<meta charset="utf-8">
<title>Brivolt Technologies – Business Card</title>
<link rel="stylesheet" href="https://fonts.googleapis.com/css2?family=Inter:wght@400;500;600&display=swap">
<style>
  :root {
    --stage: #4b4b4b;
    --card-light: #ffffff;
    --card-dark: #3d3d3d;
    --ink: #3a3a3a;
    --accent: #f7941d;
    --white: #ffffff;
  }
  html, body {
    margin: 0;
    padding: 0;
    width: 1135px;
    height: 1200px;
    overflow: hidden;
    background: var(--stage);
    font-family: "Inter", Arial, sans-serif;
  }
  .canvas {
    position: relative;
    width: 1135px;
    height: 1200px;
  }
  .card {
    position: absolute;
    left: 205px;
    width: 726px;
    height: 415px;
    overflow: hidden;
  }
  .card--front { top: 145px; background: var(--card-light); color: var(--ink); }
  .card--back  { top: 641px; background: var(--card-dark); }

  /* Wordmark */
  .wordmark {
    position: absolute;
    display: flex;
    align-items: center;
    gap: 10px;
  }
  .wordmark__square {
    background: var(--accent);
    flex: none;
  }
  .wordmark__text {
    font-weight: 600;
    line-height: 1.05;
    letter-spacing: 0.01em;
    margin: 0;
  }
  .wordmark__text span { display: block; }
  .wordmark__text .wordmark__sub { letter-spacing: 0.32em; }

  .card--front .wordmark { right: 40px; top: 38px; }
  .card--front .wordmark__square { width: 18px; height: 18px; }
  .card--front .wordmark__text { color: var(--ink); font-size: 30px; text-align: right; }
  .card--front .wordmark__sub { font-size: 11.5px; margin-top: 4px; }

  .card--back .wordmark { left: 50%; top: 50%; transform: translate(-50%, -50%); gap: 16px; }
  .card--back .wordmark__square { width: 34px; height: 34px; }
  .card--back .wordmark__text { color: var(--white); font-size: 62px; }
  .card--back .wordmark__sub { font-size: 22px; margin-top: 6px; letter-spacing: 0.33em; }

  /* Contact block */
  .contact {
    position: absolute;
    right: 40px;
    top: 193px;
    text-align: right;
  }
  .contact__name {
    margin: 0;
    color: var(--accent);
    font-size: 26px;
    font-weight: 500;
    line-height: 1;
  }
  .contact__role {
    margin: 8px 0 0;
    font-size: 17px;
    line-height: 1;
    text-transform: uppercase;
  }
  .contact__address {
    margin: 14px 0 0;
    font-style: normal;
    font-size: 17px;
    line-height: 24px;
  }
  .contact__list {
    list-style: none;
    margin: 8px 0 0;
    padding: 0;
    font-size: 17px;
    line-height: 24.5px;
  }
  .contact__list li {
    display: flex;
    justify-content: flex-end;
    align-items: center;
    gap: 7px;
  }
  .contact__icon { width: 13px; height: 13px; flex: none; }

  .edge-tab {
    position: absolute;
    right: 0;
    top: 201px;
    width: 10px;
    height: 42px;
    background: var(--accent);
  }
</style>
</head>
<body>
<main class="canvas">

  <section class="card card--front" aria-label="Business card front">
    <div class="wordmark">
      <h1 class="wordmark__text"><span>BRIVOLT</span><span class="wordmark__sub">TECHNOLOGIES</span></h1>
      <div class="wordmark__square"></div>
    </div>

    <div class="contact">
      <p class="contact__name">DANIEL HARWICK</p>
      <p class="contact__role">Director</p>
      <address class="contact__address">1417 Alder Lane<br>Fairview, MI 48621</address>
      <ul class="contact__list">
        <li>(555) 304-1872
          <svg class="contact__icon" viewBox="0 0 16 16" aria-hidden="true"><path d="M4 1.5l2.5 3-1.5 2c.8 1.8 2.2 3.2 4 4l2-1.5 3 2.5-1.5 2.5C7.5 13.5 2.5 8.5 1.5 3z" fill="none" stroke="#f7941d" stroke-width="1.6" stroke-linejoin="round"/></svg>
        </li>
        <li>info@brivolttech.com
          <svg class="contact__icon" viewBox="0 0 16 16" aria-hidden="true"><rect x="1.5" y="3.5" width="13" height="9" rx="1" fill="none" stroke="#f7941d" stroke-width="1.6"/><path d="M2 4.5l6 4.5 6-4.5" fill="none" stroke="#f7941d" stroke-width="1.6"/></svg>
        </li>
        <li>brivolttech.com
          <svg class="contact__icon" viewBox="0 0 16 16" aria-hidden="true"><g fill="none" stroke="#f7941d" stroke-width="1.3"><circle cx="8" cy="8" r="6.5"/><ellipse cx="8" cy="8" rx="3" ry="6.5"/><path d="M1.5 8h13M2.5 4.8h11M2.5 11.2h11"/></g></svg>
        </li>
      </ul>
    </div>

    <div class="edge-tab"></div>
  </section>

  <section class="card card--back" aria-label="Business card back">
    <div class="wordmark">
      <div class="wordmark__square"></div>
      <h2 class="wordmark__text"><span>BRIVOLT</span><span class="wordmark__sub">TECHNOLOGIES</span></h2>
    </div>
  </section>

</main>
</body>
</html>
```